Rosko Tamblin

I am a songwriter and would like to include a bio, pictures, discography, CD covers and access to some of my music

Target Market(s)

Music Lovers, songwriters publishers

Coding

Coded - Design and coding required

Number of Pages Required

5+ page

Requirements
Must have
• Pictures of my CD covers, pictures of me and either my Music or links to my music
Nice to have
Should not have
• cartoons

```html
<!DOCTYPE html>
<html lang="en">
<head>
<meta charset="utf-8">
<title>Rosko Tamblin – Songwriter</title>
<link rel="stylesheet" href="https://fonts.googleapis.com/css2?family=Krona+One&family=Lato:ital,wght@0,400;0,700;1,400&family=Roboto+Condensed:wght@400;700&family=Poppins:wght@400;500&display=swap">
<style>
:root{
  --black:#000;
  --white:#fff;
  --coral:#f65058;
  --muted:#d8d8d8;
  --star:#f5b400;
  --field:#1b1b1b;
}
*{box-sizing:border-box;margin:0;padding:0}
html,body{width:1200px;height:3530px;overflow:hidden;background:var(--black)}
body{position:relative;font-family:"Lato",sans-serif;color:var(--white)}
.abs{position:absolute}
.display{font-family:"Krona One",sans-serif;font-weight:400}

/* hero */
.hero{left:0;top:0;width:1200px;height:602px;
  background:radial-gradient(ellipse at 55% 70%,#ff8a1c 0%,#d24b0a 22%,#5a1404 48%,#120302 75%,#000 100%)}
.hero-person{left:600px;top:170px;width:330px;height:432px;border-radius:160px 160px 0 0;
  background:linear-gradient(180deg,#c99a85 0%,#6b4a3c 30%,#e9e4dc 55%,#2b2520 100%);opacity:.85}
.brand{left:110px;top:30px;font-size:27px;white-space:nowrap}
.nav{left:459px;top:35px;display:flex;gap:36px;font-size:16px}
.nav a{color:var(--white);text-decoration:none}
.nav a.active{color:var(--coral)}
.social{left:945px;top:31px;display:flex;gap:6px}
.social span{width:31px;height:31px;border:1.5px solid var(--white);border-radius:50%}
.hero-title{left:110px;top:205px;font-size:47px;white-space:nowrap}
.hero-text{left:111px;top:270px;width:450px;font-size:18px;line-height:32px}
.btn-solid{left:111px;top:352px;width:274px;height:60px;border-radius:30px;background:var(--coral);
  font:700 17px/60px "Lato",sans-serif;text-align:center}

/* about */
.about-ring{left:132px;top:688px;width:382px;height:392px;border-radius:50%;background:var(--coral)}
.about-photo{left:133px;top:664px;width:380px;height:414px;
  clip-path:circle(190px at 190px 224px);
  background:linear-gradient(160deg,#a88758 0%,#6d5233 45%,#f0ece4 70%,#b79d73 100%)}
.about-title{left:559px;top:700px;font-size:33px;white-space:nowrap}
.about-text{left:559px;top:755px;width:510px;font-size:14.5px;line-height:28.4px;text-align:justify}
.btn-line{border:2px solid var(--white);text-align:center;font-weight:700;color:var(--white)}
.about-btn{left:560px;top:1006px;width:186px;height:58px;border-radius:29px;line-height:54px;font-size:17px}

/* cd art */
.cdart{left:0;top:1162px;width:1200px;height:650px;
  background:radial-gradient(ellipse at 50% 35%,#5c3a6e 0%,#33203f 40%,#1a1222 75%,#0c0810 100%)}
.sec-title{width:1200px;left:0;text-align:center;font-size:35px}
.sec-sub{left:340px;width:520px;text-align:center;font-size:16px;line-height:27px;color:var(--muted)}
.disc{width:208px;height:208px;border-radius:50%}
.disc::after{content:"";position:absolute;left:96px;top:96px;width:16px;height:16px;border-radius:50%;background:var(--white)}
.disc-title{width:260px;text-align:center;font:700 22px/1 "Roboto Condensed",sans-serif;white-space:nowrap}
.disc-date{width:260px;text-align:center;font:400 18px/1 "Roboto Condensed",sans-serif}
.arrow{width:22px;height:36px}
.listen-btn{left:463px;top:1691px;width:274px;height:47px;border-radius:24px;font:700 14px/43px "Roboto Condensed",sans-serif;white-space:nowrap}

/* discography */
.cover{width:316px;height:276px}

/* reviews */
.reviews{left:0;top:2687px;width:1200px;height:441px;
  background:radial-gradient(ellipse at 50% 20%,#2b3560 0%,#1a1f3a 45%,#0b0c18 100%)}
.rev-label{left:0;width:1200px;top:2770px;text-align:center;font:500 16px/1 "Poppins",sans-serif;letter-spacing:3px}
.rev-title{top:2805px;font-size:28px}
.avatar{left:215px;top:2866px;width:104px;height:104px;border-radius:50%;background:linear-gradient(180deg,#d9d9d9,#2a3142 70%)}
.rev-name{left:167px;top:2975px;width:200px;text-align:center;font:500 17px/23px "Poppins",sans-serif}
.stars{left:240px;top:3030px;color:var(--star);font-size:11px;letter-spacing:1px}
.quote-mark{font:700 48px/1 Georgia,serif;color:#8a8fa3}
.rev-text{left:377px;top:2882px;width:600px;font-style:italic;font-size:15.5px;line-height:28.5px}
.dots{left:568px;top:3029px;display:flex;gap:5px}
.dots span{width:12px;height:12px;border-radius:50%;background:#9aa0b3}
.dots span.on{background:var(--white)}
.side-btn{top:2884px;width:84px;height:84px;border-radius:50%;background:rgba(255,255,255,.18)}

/* footer */
.foot{font-family:"Poppins",sans-serif}
.foot-h{top:3205px;font-size:15.5px;font-weight:500;white-space:nowrap}
.foot-p{font-size:14px;line-height:28px}
.field{left:425px;width:275px;height:40px;background:var(--field);font-size:14px;line-height:40px;padding-left:12px}
.subscribe{left:425px;top:3399px;width:275px;height:40px;background:var(--coral);text-align:center;font-size:15px;line-height:40px}
.foot a{color:var(--coral)}
.copy{left:0;width:1200px;top:3475px;text-align:center;font-size:14px}
</style>
</head>
<body>

<header>
  <div class="abs hero" role="img" aria-label="Photo of the songwriter standing in front of a glowing fire crater at night"></div>
  <div class="abs hero-person" role="img" aria-label="Portrait of the songwriter"></div>
  <div class="abs brand display">Rosko Tamblin</div>
  <nav class="abs nav"><a class="active" href="#">Bio</a><a href="#">Pictures</a><a href="#">Discography</a><a href="#">Cd Covers</a><a href="#">My Music</a></nav>
  <div class="abs social"><span></span><span></span><span></span><span></span></div>
  <h1 class="abs hero-title display">Rosko Tamblin</h1>
  <p class="abs hero-text">Lorem ipsum dolor sit amet, consectetur adipiscing elit, sed do eiusmod tempor incididunt</p>
  <div class="abs btn-solid">KNOW MORE ABOUT ME</div>
</header>

<section class="about">
  <div class="abs about-ring"></div>
  <div class="abs about-photo" role="img" aria-label="Photo of the songwriter in a white shirt holding a hat"></div>
  <h2 class="abs about-title display">About Rosko Tamblin</h2>
  <p class="abs about-text">Rosko Tamblin was born and raised in Houston, Texas. He began playing music at the age of eight when his sister returned home from summer camp and asked her parents to buy her a baritone ukulele. She taught her younger brother some chords on the ukulele and he was hooked. The following spring, they went to one of the border towns in Mexico and bought a Mexican guitar for $12. They restrung it with nylon strings and Tamblin began to learn how to play the guitar. He took guitar lessons at a local music store and learned how to play the hits of the day by groups like the Harbor Hounds, the Wildcards, and the Blue Lanterns.</p>
  <div class="abs btn-line about-btn">LEARN MORE</div>
</section>

<section>
  <div class="abs cdart" role="img" aria-label="Concert stage with purple and green lights"></div>
  <h2 class="abs sec-title display" style="top:1245px">CD ART</h2>
  <p class="abs sec-sub" style="top:1292px">Lorem ipsum dolor sit amet, consectetur adipiscing elit, sed do eiusmod tempor incididunt ut labore et dolore magna aliqua.</p>

  <div class="abs disc" style="left:113px;top:1375px;background:radial-gradient(circle,#bdbdbd,#3a3a3a)" role="img" aria-label="Disc art: Pines And Echoes, black and white"></div>
  <div class="abs disc" style="left:368px;top:1375px;background:radial-gradient(circle at 50% 45%,#ffb04a,#d2440c 40%,#111 75%)" role="img" aria-label="Disc art: Pines And Echoes, fire crater"></div>
  <div class="abs disc" style="left:624px;top:1375px;background:radial-gradient(circle,#e0a070,#3bbf5a 55%,#d23a8c)" role="img" aria-label="Disc art: guitar player on colourful background"></div>
  <div class="abs disc" style="left:883px;top:1375px;background:conic-gradient(#e21f26,#f5d90a,#1c3fb5,#e21f26,#f5d90a,#1c3fb5,#e21f26)" role="img" aria-label="Disc art: Open Palms, colourful painted pattern"></div>

  <div class="abs disc-title" style="left:87px;top:1607px">Pines And Echoes</div>
  <div class="abs disc-date" style="left:87px;top:1639px">5-4-19</div>
  <div class="abs disc-title" style="left:342px;top:1607px">Pines And Echoes</div>
  <div class="abs disc-date" style="left:342px;top:1639px">5-4-19</div>
  <div class="abs disc-title" style="left:604px;top:1607px">Roskos&nbsp; CD</div>
  <div class="abs disc-date" style="left:604px;top:1639px">5-4-19</div>
  <div class="abs disc-title" style="left:861px;top:1607px">Open Palms</div>
  <div class="abs disc-date" style="left:861px;top:1639px">11-9-19</div>

  <svg class="abs arrow" style="left:61px;top:1470px" viewBox="0 0 22 36"><path d="M18 2 L4 18 L18 34" fill="none" stroke="#fff" stroke-width="2"/></svg>
  <svg class="abs arrow" style="left:1114px;top:1470px" viewBox="0 0 22 36"><path d="M4 2 L18 18 L4 34" fill="none" stroke="#fff" stroke-width="2"/></svg>

  <div class="abs btn-line listen-btn">LISTEN FROM CURIOUS SEASONS</div>
</section>

<section>
  <h2 class="abs sec-title display" style="top:1890px">DISCOGRAPHY</h2>
  <p class="abs sec-sub" style="top:1938px">Lorem ipsum dolor sit amet, consectetur adipiscing elit, sed do eiusmod tempor incididunt ut labore et dolore magna aliqua.</p>

  <div class="abs cover" style="left:110px;top:2024px;background:linear-gradient(180deg,#6a6f85,#3c3340 50%,#a2431c)" role="img" aria-label="Album cover: Curious Seasons, stormy sky and silhouette"></div>
  <div class="abs cover" style="left:441px;top:2024px;background:linear-gradient(180deg,#000 0%,#111 30%,#e0561a 45%,#000 60%)" role="img" aria-label="Album cover: The Pines And The Echoes"></div>
  <div class="abs cover" style="left:771px;top:2024px;background:conic-gradient(from 40deg,#e21f26,#f5d90a,#1c3fb5,#e21f26,#f5d90a,#1c3fb5,#e21f26)" role="img" aria-label="Album cover: Open Palms"></div>
  <div class="abs cover" style="left:110px;top:2314px;background:linear-gradient(150deg,#f3efc8,#dcd2e6 50%,#d9c79a)" role="img" aria-label="Album cover: Back When I Was Small"></div>
  <div class="abs cover" style="left:441px;top:2314px;background:linear-gradient(135deg,#e8399a,#f4d040 40%,#35b4d8 70%,#b74be0)" role="img" aria-label="Album cover: The Roskos, guitarist on swirl background"></div>
  <div class="abs cover" style="left:771px;top:2314px;background:linear-gradient(180deg,#6f7b8a,#3d4b58 45%,#c9d2d8 75%,#38434c)" role="img" aria-label="Album cover: Harbor Lights, ocean wave"></div>
</section>

<section>
  <div class="abs reviews" role="img" aria-label="Concert crowd under stage lights"></div>
  <div class="abs rev-label">REVIEWS</div>
  <h2 class="abs sec-title display rev-title">WHAT OUR CUSTOMERS ARE SAYING</h2>
  <div class="abs side-btn" style="left:-36px"></div>
  <div class="abs side-btn" style="left:1152px"></div>
  <svg class="abs" style="left:8px;top:2916px" width="14" height="22" viewBox="0 0 14 22"><path d="M12 1 L2 11 L12 21" fill="none" stroke="#fff" stroke-width="1.6"/></svg>
  <svg class="abs" style="left:1178px;top:2916px" width="14" height="22" viewBox="0 0 14 22"><path d="M2 1 L12 11 L2 21" fill="none" stroke="#fff" stroke-width="1.6"/></svg>
  <div class="abs avatar" role="img" aria-label="Reviewer portrait"></div>
  <div class="abs rev-name">Marco Feltri,<br>Kettle Studio Bass</div>
  <div class="abs stars">★★★★★</div>
  <div class="abs quote-mark" style="left:340px;top:2872px">“</div>
  <p class="abs rev-text">At this point I have developed a continuous creative relationship with Rosko and have recorded on approximately 30 songs of his. He writes well-structured songs that allow me to flex my creative muscles. Rosko knows how to make his original ideas blossom into fully constructed arrangements that sound great</p>
  <div class="abs quote-mark" style="left:780px;top:2975px">”</div>
  <div class="abs dots"><span class="on"></span><span></span><span></span><span></span></div>
</section>

<footer class="foot">
  <h3 class="abs foot-h" style="left:113px">CONTACT US</h3>
  <p class="abs foot-p" style="left:113px;top:3241px">123 Avenue name, City name<br>10150, United States</p>
  <p class="abs foot-p" style="left:113px;top:3299px">888 888 8888<br>info@roskotamblin.com</p>

  <h3 class="abs foot-h" style="left:428px">ROSKO TAMBLIN NEWSLETTER</h3>
  <p class="abs foot-p" style="left:424px;top:3241px;width:290px">Lorem ipsum dolor sit amet, consectetur adipiscing elit, sed do eiusmod</p>
  <div class="abs field" style="top:3310px">Name</div>
  <div class="abs field" style="top:3356px">Email</div>
  <div class="abs subscribe">SUBSCRIBE</div>

  <h3 class="abs foot-h" style="left:808px">OUR LATEST MUSIC</h3>
  <p class="abs foot-p" style="left:807px;top:3241px;width:300px">Lorem ipsum dolor sit amet, consectetur adipiscing elit, sed do eiuor , consectetur adipiscing elit, <a href="#">Read More</a></p>

  <p class="abs copy">Copyright © 2020. All Rights Reserved</p>
</footer>

</body>
</html>
```